Kestrel Motion LLC Sports Therapy and Soft Tissue Injury solutions

We are a company that specializes in Sports Therapy, Physical therapy, muscular rehab, nutrition plans, and personal training. Kestrel Motion travels around the country and world treating athletes and people in the workforce that have Soft Tissue injuries. We are legally partnered with VMR(Vantor Muscle Recovery/vantorrecovery.example) in treating endurance athletes ex. SteelRidge triathalon. We educate our patients on how to sustain a healthy lifestyle.We need a web design that has a Home page summarizing our services, a Physical therapy page, a Personal training and nutrition page. Our ultimate goal is to build relationships with fitness centers, training facilities, and companies that are implementing preventative health measures for their employees. We want to incorporate the VMR logo and Steelridge logo attached in the website but, we want to use our own name (Kestrel Motion LLC) as the main draw. We will provide literature for the website.

Target Market(s)

Grindlane training gyms, Fitness centers, Dance studios, Companies looking for Corporate Wellness programs

Industry/Entity Type

Health And Wellness

Number of Pages Required

4 page

Font styles to use
Sans Serif

Requirements
Must have
• Stock Photos of Athletes training. Examples of Endurance Athletes and Cross training. A mesh of as many sports and training methods as possible. We are a new company and don't have many photos. Easy accessibility to change and add text as the company grows. Vantor Muscle recovery logo incorporated in the back ground of the website. Always visible but does not take over the web page
Nice to have
• Sleek and cool, and masculine design. We want the website to stand out without focusing on one individual. We want to use the website to brand the company (Kestrel Motion LLC) with easy access to social media platforms

```html
<!DOCTYPE html>
<html lang="en">
<head>
<meta charset="utf-8">
<title>Kestrel Motion LLC – Sports Therapy and Soft Tissue Injury Solutions</title>
<link rel="stylesheet" href="https://fonts.googleapis.com/css2?family=Roboto:wght@300;400;500;700&family=Roboto+Condensed:wght@400;700&display=swap">
<style>
:root{
  --blue:#1e88d6;
  --blue-dark:#0f5ea8;
  --blue-deep:#0a4886;
  --ink:#222222;
  --text:#6b6b6b;
  --muted:#9a9a9a;
  --line:#e3e3e3;
  --paper:#ffffff;
  --soft:#f2f2f2;
  --orange:#f47c20;
  --dark:#1b1d20;
}
*{box-sizing:border-box;margin:0;padding:0}
html,body{width:1200px;height:3000px;overflow:hidden}
body{font-family:"Roboto",Arial,sans-serif;color:var(--text);background:var(--paper);font-size:13px;line-height:1.6;position:relative}
.wrap{width:1000px;margin:0 auto;position:relative}
h1,h2,h3,h4{font-family:"Roboto Condensed","Roboto",sans-serif;color:var(--ink);font-weight:700}

/* header */
.site-header{height:110px}
.site-header .wrap{display:flex;justify-content:space-between;align-items:center;height:110px}
.brand{display:flex;align-items:center;gap:12px}
.brand-mark{width:34px;height:34px;border-radius:50%;background:var(--blue)}
.brand-name{font-size:30px;font-weight:700;color:var(--blue-dark);letter-spacing:.3px}
.header-contact{display:flex;align-items:center;gap:18px}
.header-contact .lines{font-size:12px;color:var(--text);line-height:1.7}
.header-contact svg{width:22px;height:22px}
.social-dots{display:flex;gap:6px}
.social-dots span{width:22px;height:22px;border-radius:50%;background:var(--blue)}
.social-dots span:nth-child(2){background:#3fa9e6}
.social-dots span:nth-child(3){background:#d9534f}
.social-dots span:nth-child(4){background:#c4302b}

/* nav */
.main-nav{height:40px;background:var(--blue)}
.main-nav ul{list-style:none;display:flex;height:40px}
.main-nav li{padding:0 20px;line-height:40px;color:#fff;font-size:12px;font-weight:500;letter-spacing:.4px}
.main-nav li.active{background:var(--blue-dark)}

/* hero */
.hero{height:500px;background:linear-gradient(100deg,#6f7d58 0%,#9aa37c 30%,#7b6a57 55%,#3e4a35 80%,#2f3a2c 100%);position:relative}
.hero-copy{position:absolute;left:720px;top:150px;width:360px;color:#fff}
.hero-copy h1{color:#fff;font-size:38px;letter-spacing:1px;margin-bottom:8px}
.hero-copy p{font-size:13px;color:#eef2e8}

/* feature cards */
.feature-cards{position:absolute;top:560px;left:120px;display:flex;gap:30px}
.feature-card{width:300px;height:310px;background:#fff;box-shadow:0 3px 14px rgba(0,0,0,.18);text-align:center}
.feature-card h3{font-size:18px;font-weight:400;height:44px;line-height:44px}
.feature-card .photo{height:140px}
.feature-card p{font-size:11.5px;padding:14px 18px 8px;color:var(--text);line-height:1.55}
.more{font-size:10px;font-weight:700;color:var(--ink);letter-spacing:.5px;display:inline-flex;align-items:center;gap:5px}
.more i{display:inline-block;width:11px;height:11px;border-radius:50%;background:var(--ink);position:relative}
.more i::after{content:"";position:absolute;left:3px;top:3px;border:2.5px solid transparent;border-left:4px solid #fff}
.ph-therapy{background:linear-gradient(135deg,#c9d4dc,#8ca0b1)}
.ph-training{background:linear-gradient(135deg,#9cb07a,#5d7146)}
.ph-nutrition{background:linear-gradient(135deg,#e4efe4,#9cc6a0)}

/* welcome */
.welcome{padding-top:290px;height:770px}
.welcome .wrap{display:flex;gap:60px;align-items:flex-start}
.welcome-photo{flex:0 0 240px;height:240px;border-radius:50%;background:linear-gradient(135deg,#b9c7a4,#6f8a5a);border:6px solid #fff;box-shadow:0 0 0 1px var(--line);margin-top:20px}
.welcome h2{font-size:34px;line-height:1.1;margin-bottom:4px}
.welcome h2 .accent{color:var(--blue)}
.welcome .rule{width:60px;height:3px;background:var(--blue);margin:12px 0 18px}
.welcome p{font-size:13px;margin-bottom:16px}

/* services */
.services-band{height:330px;background:linear-gradient(90deg,#202326 0%,#34383b 45%,#262a2d 70%,#151719 100%);text-align:center;color:#d8d8d8;padding-top:80px}
.services-band h2{color:#fff;font-size:36px;letter-spacing:1px}
.services-band .rule{width:60px;height:3px;background:var(--blue);margin:10px auto 18px}
.services-band p{width:760px;margin:0 auto;font-size:13px}
.service-list{display:flex;justify-content:space-between;margin-top:-50px;position:relative}
.service{width:230px;text-align:center}
.service .icon{width:96px;height:96px;border-radius:50%;background:#fff;border:1px solid var(--line);margin:0 auto;display:flex;align-items:center;justify-content:center;box-shadow:0 2px 8px rgba(0,0,0,.12)}
.service .icon svg{width:44px;height:44px}
.service h4{font-size:18px;font-weight:400;margin:16px 0 6px}
.service .rule{width:40px;height:2px;background:var(--blue);margin:0 auto 10px}
.service p{font-size:12px;margin-bottom:10px}

/* newsletter */
.newsletter{margin-top:60px;height:120px;background:var(--soft)}
.newsletter .wrap{display:flex;align-items:center;height:120px;gap:16px}
.newsletter .mail{width:50px;height:50px;border-radius:50%;background:var(--orange);display:flex;align-items:center;justify-content:center}
.newsletter h3{font-size:22px;font-weight:400}
.newsletter .sub{font-size:12px;color:var(--muted)}
.newsletter form{margin-left:auto;display:flex}
.newsletter .field{width:300px;height:40px;background:#fff;border:1px solid var(--line);padding:0 14px;line-height:38px;color:var(--muted);font-size:12px}
.newsletter .btn{height:40px;padding:0 26px;background:var(--orange);color:#fff;font-weight:700;font-size:12px;line-height:40px;letter-spacing:.5px}

/* news */
.news{padding-top:50px;height:510px}
.news-head{display:flex;justify-content:space-between;align-items:center}
.news-head h2{font-size:30px}
.arrows{display:flex;gap:6px}
.arrows span{width:24px;height:24px;background:var(--soft);display:flex;align-items:center;justify-content:center}
.news .rule{width:60px;height:3px;background:var(--blue);margin:10px 0 30px}
.news-list{display:flex;gap:40px}
.news-item{flex:1;display:flex;gap:22px}
.news-item .photo{flex:0 0 200px;height:240px}
.ph-knee{background:linear-gradient(135deg,#e9cdb7,#b98c6c)}
.ph-coach{background:linear-gradient(135deg,#dfe6ee,#9fb1c4)}
.news-item h4{font-size:17px;font-weight:400;line-height:1.35;margin-top:14px}
.news-item .date{display:inline-block;margin:10px 0;padding:2px 8px;background:var(--blue);color:#fff;font-size:11px}
.news-item p{font-size:12px;margin-bottom:10px}

/* footer */
.site-footer{position:absolute;left:0;top:2690px;width:1200px;height:310px}
.footer-wave{position:absolute;top:0;left:0;width:1200px;height:60px}
.footer-body{position:absolute;top:50px;left:0;width:1200px;height:220px;background:var(--blue-dark);color:#d6e6f5}
.footer-body .wrap{display:flex;gap:40px;padding-top:24px}
.footer-col{flex:1}
.footer-col h4{color:#fff;font-size:18px;margin-bottom:6px}
.footer-col .rule{width:40px;height:2px;background:#fff;margin-bottom:14px}
.footer-col p,.footer-col li{font-size:12px;line-height:1.9;list-style:none}
.footer-col li::before{content:"›";margin-right:8px;color:#fff}
.contact-row{display:flex;align-items:center;gap:8px}
.contact-row svg{width:14px;height:14px;flex:none}
.map{width:220px;height:120px;background:linear-gradient(135deg,#e6ecef,#c7d3d9)}
.social-list li::before{content:none}
.social-list li{display:flex;align-items:center;gap:8px}
.social-list li span{width:14px;height:14px;border-radius:50%;background:#fff;opacity:.85}
.copyright{position:absolute;bottom:0;left:0;width:1200px;height:40px;background:var(--blue-deep);color:#bcd3ea;font-size:11px}
.copyright .wrap{line-height:40px}
</style>
</head>
<body>

<header class="site-header">
  <div class="wrap">
    <div class="brand">
      <span class="brand-mark"></span>
      <span class="brand-name">Kestrel Motion LLC</span>
    </div>
    <div class="header-contact">
      <svg viewBox="0 0 24 24" aria-hidden="true"><path d="M6.6 10.8a15.1 15.1 0 0 0 6.6 6.6l2.2-2.2a1 1 0 0 1 1-.25 11.4 11.4 0 0 0 3.6.57 1 1 0 0 1 1 1V20a1 1 0 0 1-1 1A17 17 0 0 1 3 4a1 1 0 0 1 1-1h3.5a1 1 0 0 1 1 1c0 1.25.2 2.45.57 3.57a1 1 0 0 1-.25 1z" fill="#1e88d6"/></svg>
      <div class="lines">info@kestrelmotion.example<br>Phone : (555) 014-2290</div>
      <div class="social-dots"><span></span><span></span><span></span><span></span></div>
    </div>
  </div>
</header>

<nav class="main-nav">
  <div class="wrap">
    <ul>
      <li class="active">HOME</li>
      <li>SERVICES</li>
      <li>PHYSICAL THERAPY</li>
      <li>PERSONAL TRAINING</li>
      <li>NUTRITION</li>
      <li>BLOG</li>
      <li>CONTACT US</li>
    </ul>
  </div>
</nav>

<section class="hero" role="img" aria-label="Athlete running outdoors on a track during training">
  <div class="hero-copy">
    <h1>ATHLETES TRAINING</h1>
    <p>Strength, endurance and recovery programs built for athletes who train hard and want to keep moving without injury.</p>
  </div>
</section>

<div class="feature-cards">
  <article class="feature-card">
    <h3>Physical Therapy</h3>
    <div class="photo ph-therapy" role="img" aria-label="Therapist working with a client on an exercise ball"></div>
    <p>Hands-on care that restores range of motion, eases soft tissue pain and gets you back to full training sooner.</p>
    <span class="more">CLICK MORE <i></i></span>
  </article>
  <article class="feature-card">
    <h3>Personal Training</h3>
    <div class="photo ph-training" role="img" aria-label="Trainer coaching a client through an outdoor workout"></div>
    <p>Coached sessions for endurance, strength and cross training, planned around your sport, schedule and current fitness level.</p>
    <span class="more">CLICK MORE <i></i></span>
  </article>
  <article class="feature-card">
    <h3>Nutrition</h3>
    <div class="photo ph-nutrition" role="img" aria-label="Nutrition consultant holding fresh fruit"></div>
    <p>Simple meal plans that fuel hard training days, speed up recovery and support a healthy lifestyle for the long run.</p>
    <span class="more">CLICK MORE <i></i></span>
  </article>
</div>

<section class="welcome">
  <div class="wrap">
    <div class="welcome-photo" role="img" aria-label="Two people training together outdoors"></div>
    <div class="welcome-copy">
      <h2>WELCOME TO<br><span class="accent">KESTREL MOTION LLC</span></h2>
      <div class="rule"></div>
      <p>Kestrel Motion travels across the country and around the world to treat athletes and working people with soft tissue injuries. Our therapists combine sports therapy, muscular rehab and guided training so every client leaves with a clear plan, stronger habits and the tools to stay active.</p>
      <p>We partner with fitness centers, training facilities, dance studios and companies building wellness programs for their teams. Through our work with Vantor Muscle Recovery we support endurance athletes preparing for events such as the Steelridge triathlon, and we teach every patient how to sustain a healthy lifestyle.</p>
    </div>
  </div>
</section>

<section class="services-band" role="img" aria-label="Dark background of a sprinter on a running track">
  <h2>OUR SERVICES</h2>
  <div class="rule"></div>
  <p>From first assessment to race day, we treat the cause of pain, rebuild strength and keep athletes, dancers and busy teams performing at their best.</p>
</section>

<div class="wrap">
  <div class="service-list">
    <div class="service">
      <div class="icon"><svg viewBox="0 0 48 48" fill="none" stroke="#333" stroke-width="2.5" stroke-linecap="round"><circle cx="24" cy="27" r="14"/><path d="M24 27V18M20 8h8M24 8v5"/></svg></div>
      <h4>Sports Therapy</h4><div class="rule"></div>
      <p>Targeted treatment for strains, tendon pain and overuse injuries from sport.</p>
      <span class="more">READ MORE <i></i></span>
    </div>
    <div class="service">
      <div class="icon"><svg viewBox="0 0 48 48" fill="none" stroke="#333" stroke-width="2.5" stroke-linecap="round" stroke-linejoin="round"><path d="M4 26h10l5-12 8 22 5-10h12"/></svg></div>
      <h4>Muscular Rehab</h4><div class="rule"></div>
      <p>Step-by-step rehab that rebuilds muscle strength and joint stability.</p>
      <span class="more">READ MORE <i></i></span>
    </div>
    <div class="service">
      <div class="icon"><svg viewBox="0 0 48 48" fill="none" stroke="#333" stroke-width="2.5" stroke-linecap="round"><path d="M6 24h36a18 14 0 0 1-36 0z"/><path d="M18 18c0-5 4-8 8-10M28 18c2-4 6-6 10-6"/></svg></div>
      <h4>Nutrition Plans</h4><div class="rule"></div>
      <p>Meal guidance that matches your training load and recovery needs.</p>
      <span class="more">READ MORE <i></i></span>
    </div>
    <div class="service">
      <div class="icon"><svg viewBox="0 0 48 48" fill="none" stroke="#333" stroke-width="2.5" stroke-linecap="round"><path d="M14 24h20"/><rect x="7" y="15" width="7" height="18" rx="1"/><rect x="34" y="15" width="7" height="18" rx="1"/><path d="M3 20v8M45 20v8"/></svg></div>
      <h4>Personal Training</h4><div class="rule"></div>
      <p>One-on-one coaching for endurance, strength and cross training.</p>
      <span class="more">READ MORE <i></i></span>
    </div>
  </div>
</div>

<section class="newsletter">
  <div class="wrap">
    <div class="mail"><svg width="26" height="26" viewBox="0 0 24 24" fill="none" stroke="#fff" stroke-width="2"><rect x="3" y="5" width="18" height="14" rx="1"/><path d="M3 6l9 7 9-7"/></svg></div>
    <div>
      <h3>Join Our Newsletter.</h3>
      <div class="sub">Sign up to stay with the latest news.</div>
    </div>
    <form>
      <div class="field">E-mail</div>
      <div class="btn">SUBSCRIBE</div>
    </form>
  </div>
</section>

<section class="news">
  <div class="wrap">
    <div class="news-head">
      <h2>LATEST NEWS</h2>
      <div class="arrows">
        <span><svg width="10" height="10" viewBox="0 0 10 10"><path d="M7 1L3 5l4 4" stroke="#555" stroke-width="1.6" fill="none"/></svg></span>
        <span><svg width="10" height="10" viewBox="0 0 10 10"><path d="M3 1l4 4-4 4" stroke="#555" stroke-width="1.6" fill="none"/></svg></span>
      </div>
    </div>
    <div class="rule"></div>
    <div class="news-list">
      <article class="news-item">
        <div class="photo ph-knee" role="img" aria-label="Close view of a knee being treated"></div>
        <div>
          <h4>Five recovery habits every endurance athlete should build</h4>
          <span class="date">JAN 26, 2017</span>
          <p>Rest days, sleep, mobility work and steady fueling do more for your race results than one extra hard session.</p>
          <span class="more">Read More <i></i></span>
        </div>
      </article>
      <article class="news-item">
        <div class="photo ph-coach" role="img" aria-label="Coach standing in a fitness studio"></div>
        <div>
          <h4>How corporate wellness programs cut soft tissue injuries</h4>
          <span class="date">JAN 26, 2017</span>
          <p>Short daily movement breaks and early treatment keep teams healthy, lower sick days and build a stronger workplace.</p>
          <span class="more">Read More <i></i></span>
        </div>
      </article>
    </div>
  </div>
</section>

<footer class="site-footer">
  <svg class="footer-wave" viewBox="0 0 1200 60" preserveAspectRatio="none" aria-hidden="true">
    <path d="M0 30 C300 0 600 60 900 25 C1020 12 1120 18 1200 28 V60 H0z" fill="#1e88d6"/>
    <path d="M0 45 C300 20 600 70 900 40 C1020 30 1120 34 1200 42 V60 H0z" fill="#0f5ea8"/>
  </svg>
  <div class="footer-body">
    <div class="wrap">
      <div class="footer-col">
        <h4>CONTACT US</h4><div class="rule"></div>
        <p>Kestrel Motion LLC, 412 Harbor Ave,<br>Suite 8, Riverton, CO 80401</p>
        <p class="contact-row"><svg viewBox="0 0 24 24"><path d="M6.6 10.8a15.1 15.1 0 0 0 6.6 6.6l2.2-2.2a1 1 0 0 1 1-.25 11.4 11.4 0 0 0 3.6.57 1 1 0 0 1 1 1V20a1 1 0 0 1-1 1A17 17 0 0 1 3 4a1 1 0 0 1 1-1h3.5a1 1 0 0 1 1 1c0 1.25.2 2.45.57 3.57a1 1 0 0 1-.25 1z" fill="#fff"/></svg>(555) 014-2290</p>
        <p class="contact-row"><svg viewBox="0 0 24 24" fill="none" stroke="#fff" stroke-width="2"><rect x="3" y="5" width="18" height="14"/><path d="M3 6l9 7 9-7"/></svg>info@kestrelmotion.example</p>
      </div>
      <div class="footer-col">
        <h4>QUICK LINKS</h4><div class="rule"></div>
        <ul>
          <li>Home</li><li>Services</li><li>Physical Therapy</li><li>Personal Training</li><li>Nutrition</li><li>Contact us</li>
        </ul>
      </div>
      <div class="footer-col">
        <h4>OUR LOCATION</h4><div class="rule"></div>
        <div class="map" role="img" aria-label="Street map showing the office location"></div>
      </div>
      <div class="footer-col">
        <h4>SOCIAL</h4><div class="rule"></div>
        <ul class="social-list">
          <li><span></span>Community</li><li><span></span>Updates</li><li><span></span>Network</li><li><span></span>Videos</li>
        </ul>
      </div>
    </div>
  </div>
  <div class="copyright"><div class="wrap">© 2017 Copyright Kestrel Motion LLC. All Rights Reserved.</div></div>
</footer>

</body>
</html>
```